Halberd Guard Services

Our Company is a security business which needs a cut edge design, the final product should have all relevant information and maintain a bold but modern and professional look.

Target Market(s)

A cut edge design which will attract any audience

Industry/Entity Type

Security

Contact Information for Business Card

HALBERD GUARD SERVICES

Gregor Lindqvist
Operations Manager
Phone: 0491 735 219

Email: info@halberdguard.com.au
Web: www.halberdguard.com.au

Requirements
Must have
• Must be double sided and contain all relevant information and the company logo.

```html
<!DOCTYPE html>
<html lang="en">
<head>
<meta charset="utf-8">
<title>Halberd Guard Services – Business Card</title>
<link rel="stylesheet" href="https://fonts.googleapis.com/css2?family=Open+Sans:wght@400;600;700&display=swap">
<style>
  :root {
    --backdrop: #e4e5e7;
    --card: #ffffff;
    --card-shade: #f1f2f3;
    --slate: #3c4d53;
    --ink: #1f2426;
    --orange: #f39a1e;
    --rule: #4f6b72;
  }
  * { box-sizing: border-box; margin: 0; padding: 0; }
  html, body {
    width: 1200px; height: 951px; overflow: hidden;
    background: var(--backdrop);
    font-family: "Open Sans", Verdana, sans-serif;
  }
  .canvas { position: relative; width: 1200px; height: 951px; }
  .card {
    position: absolute; width: 520px; height: 300px;
    background: var(--card); border-radius: 18px;
    box-shadow: 0 6px 18px rgba(0,0,0,.18);
    overflow: hidden;
  }
  .card--front { left: 70px; top: 150px;
    background: linear-gradient(200deg, var(--card-shade) 0%, var(--card) 45%); }
  .card--back { left: 610px; top: 490px; }

  .brand { display: flex; align-items: center; gap: 12px; }
  .brand__mark { width: 40px; height: 40px; background: var(--slate); border-radius: 6px; flex: none; }
  .brand__name { color: var(--slate); font-weight: 700; letter-spacing: .5px; white-space: nowrap; }

  .card--front .brand { position: absolute; left: 40px; top: 124px; }
  .card--front .brand__mark { width: 52px; height: 52px; }
  .card--front .brand__name { font-size: 30px; }

  .card--back .brand { position: absolute; left: 26px; top: 28px; }
  .card--back .brand__mark { width: 32px; height: 32px; }
  .card--back .brand__name { font-size: 20px; }

  .divider { position: absolute; left: 26px; right: 20px; top: 120px;
    height: 1px; background: var(--rule); }

  .person { position: absolute; right: 24px; top: 96px; text-align: right; }
  .person__name { color: var(--orange); font-size: 17px; font-weight: 400; line-height: 22px; }
  .person__role { color: var(--ink); font-size: 13px; line-height: 18px; margin-top: 6px; }

  .contacts { position: absolute; left: 20px; top: 196px; list-style: none;
    font-size: 14px; color: var(--ink); line-height: 22px; }
  .contacts li { display: flex; align-items: center; gap: 8px; white-space: nowrap; }
  .contacts svg { width: 12px; height: 12px; flex: none; }
</style>
</head>
<body>
<main class="canvas">
  <section class="card card--front" aria-label="Card front">
    <div class="brand">
      <span class="brand__mark"></span>
      <span class="brand__name">HALBERD GUARD SERVICES</span>
    </div>
  </section>

  <section class="card card--back" aria-label="Card back">
    <div class="brand">
      <span class="brand__mark"></span>
      <span class="brand__name">HALBERD GUARD SERVICES</span>
    </div>
    <div class="divider"></div>
    <div class="person">
      <p class="person__name">Gregor Lindqvist</p>
      <p class="person__role">Operations Manager</p>
    </div>
    <ul class="contacts">
      <li><svg viewBox="0 0 12 12"><path d="M3 1l2 2-1 1.5c.6 1.4 1.6 2.4 3 3L8.5 6.5l2 2-1.5 1.5C5.5 10 2 6.5 1.5 2.5z" fill="var(--orange)"/></svg>0491 735 219</li>
      <li><svg viewBox="0 0 12 12"><rect x="1" y="3" width="10" height="7" rx="1" fill="none" stroke="var(--orange)" stroke-width="1.4"/><path d="M1.5 3.5L6 7l4.5-3.5" fill="none" stroke="var(--orange)" stroke-width="1.2"/></svg>info@halberdguard.com.au</li>
      <li><svg viewBox="0 0 12 12"><circle cx="6" cy="6" r="5" fill="var(--orange)"/></svg>www.halberdguard.com.au</li>
    </ul>
  </section>
</main>
</body>
</html>
```